Need Business Card for our Real Estate Business with Sales Executive's Picture

PANTONE 484 C ( RED)

PANTONE 2766 C ( BLUE

Industry/Entity Type

Real Estate

Contact Information for Business Card

Name, Mobile, email, & picture of Person
Agency Phone, address, Web address

Requirements
Must have
• Our Logo Colours, Agent Picture,

```html
<!DOCTYPE html>
<html lang="en">
<head>
<meta charset="utf-8">
<title>Dunmore Realty – Business Card</title>
<link href="https://fonts.googleapis.com/css2?family=Work+Sans:wght@400;500;600&display=swap" rel="stylesheet">
<style>
  :root {
    --navy: #0b1a45;
    --red: #7a1020;
    --white: #ffffff;
    --backdrop: #e4e5e8;
    --photo-top: #dfe3ea;
    --photo-suit: #2a3f8f;
    --text-light: #ffffff;
    --text-soft: #d8dcea;
  }
  * { box-sizing: border-box; margin: 0; padding: 0; }
  html, body { width: 1200px; height: 900px; overflow: hidden; }
  body {
    background: var(--backdrop);
    font-family: "Work Sans", sans-serif;
    position: relative;
  }
  .card {
    position: absolute;
    left: 280px;
    width: 640px;
    height: 366px;
    border-radius: 22px;
    overflow: hidden;
    background: var(--white);
    box-shadow: 0 10px 28px rgba(0,0,0,0.18);
  }
  .card--front { top: 64px; }
  .card--back { top: 470px; }

  .agent-photo {
    position: absolute;
    left: 0; top: 0;
    width: 270px; height: 366px;
    background: linear-gradient(180deg, var(--photo-top) 0%, #b9c3dc 35%, var(--photo-suit) 70%, #1c2d6e 100%);
  }

  .logo-area {
    position: absolute;
    top: 0; bottom: 0;
    display: flex;
    align-items: center;
    justify-content: center;
  }
  .card--front .logo-area { left: 270px; right: 0; padding-top: 40px; }
  .card--back .logo-area { left: 330px; right: 16px; }

  .brand {
    display: flex;
    align-items: center;
    gap: 10px;
    color: var(--navy);
    font-weight: 500;
    letter-spacing: 0.06em;
    white-space: nowrap;
  }
  .brand__mark {
    width: 12px; height: 12px;
    background: var(--red);
    flex: none;
  }
  .card--front .brand { font-size: 24px; }
  .card--back .brand { font-size: 22px; }

  .back-art { position: absolute; inset: 0; }

  .contact {
    position: absolute;
    left: 36px; top: 70px;
    color: var(--text-light);
  }
  .contact__name { font-size: 22px; font-weight: 600; letter-spacing: 0.02em; }
  .contact__role { font-size: 14px; color: var(--text-soft); margin-top: 2px; }
  .contact__address { font-size: 14px; line-height: 1.4; margin-top: 18px; }
  .contact__list { list-style: none; margin-top: 14px; font-size: 14px; line-height: 1.7; }
  .contact__list li { display: flex; align-items: center; gap: 10px; }
  .contact__list svg { width: 12px; height: 12px; flex: none; }
</style>
</head>
<body>

<section class="card card--front">
  <div class="agent-photo" role="img" aria-label="Portrait photo of the sales executive in a navy suit and striped tie"></div>
  <div class="logo-area">
    <div class="brand"><span class="brand__mark"></span>DUNMORE REALTY</div>
  </div>
</section>

<section class="card card--back">
  <svg class="back-art" viewBox="0 0 640 366" width="640" height="366" aria-hidden="true">
    <path d="M0 0 H322 Q236 200 452 366 H0 Z" fill="var(--red)"/>
    <path d="M0 0 H300 Q222 205 420 366 H0 Z" fill="var(--navy)" stroke="var(--white)" stroke-width="4"/>
  </svg>

  <div class="contact">
    <p class="contact__name">DANIEL BROOKS</p>
    <p class="contact__role">Managing Director</p>
    <p class="contact__address">Via Colle Verde,<br>148, 12030 Roveta (CN)</p>
    <ul class="contact__list">
      <li>
        <svg viewBox="0 0 16 16"><path d="M4 1 L6.5 4.5 L5 6.5 Q6.5 9.5 9.5 11 L11.5 9.5 L15 12 L13 15 Q6 14 1 3 Z" fill="currentColor"/></svg>
        +852 2041 5567
      </li>
      <li>
        <svg viewBox="0 0 16 16"><rect x="2" y="3" width="12" height="10" rx="1.5" fill="currentColor"/></svg>
        +852 2041 5590
      </li>
      <li>
        <svg viewBox="0 0 16 16"><rect x="1.5" y="3.5" width="13" height="9" fill="none" stroke="currentColor" stroke-width="1.5"/><path d="M1.5 3.5 L8 9 L14.5 3.5" fill="none" stroke="currentColor" stroke-width="1.5"/></svg>
        info@dunmorerealty.com
      </li>
      <li>
        <svg viewBox="0 0 16 16"><circle cx="8" cy="8" r="6.5" fill="none" stroke="currentColor" stroke-width="1.5"/><path d="M1.5 8 H14.5 M8 1.5 Q4 8 8 14.5 Q12 8 8 1.5" fill="none" stroke="currentColor" stroke-width="1.2"/></svg>
        www.dunmorerealty.com
      </li>
    </ul>
  </div>

  <div class="logo-area">
    <div class="brand"><span class="brand__mark"></span>DUNMORE REALTY</div>
  </div>
</section>

</body>
</html>
```